Business Card Design for Flood Rescue 360 - Property Restoration Professionals

I need a business card designed for Flood Rescue 360. We are a full-service property restoration solution. Providing water, fire, smoke & storm restoration as well as mold remediation and full remodel or reconstruction to homes and businesses across Dallas-Fort Worth, TX.
Target Market(s)
home and business owners with insurance covered property damage from water, fire or storm related damage
Industry/Entity Type
property restoration
Contact Information for Business Card
Marcus Pelley General Manager Cell: 214-555-0193 Office: 469-555-0148 email: Marcus@FloodRescue360.example services: Water, Fire, Mold, Reconstruction Tagline: Urgency for Your Water Emergency!
Look and feel
Each slider illustrates characteristics of the customer's brand and the style your logo design should communicate.

```html
<!DOCTYPE html>
<html lang="en">
<head>
<meta charset="utf-8">
<title>Flood Rescue 360 — Business Card</title>
<link rel="stylesheet" href="https://fonts.googleapis.com/css2?family=Montserrat:wght@400;500;700;800&display=swap">
<style>
  :root {
    --backdrop: #1c1c1c;
    --card-white: #f4f4f4;
    --brand-blue: #16ace0;
    --ink: #1e1e1e;
    --card-dark: #262626;
    --pattern-light: #5d5d5d;
    --back-text: #f2f2f2;
  }
  * { margin: 0; padding: 0; box-sizing: border-box; }
  html, body { width: 1200px; height: 1059px; overflow: hidden; background: var(--backdrop); }
  body { position: relative; font-family: "Montserrat", sans-serif; }

  .card { position: absolute; left: 256px; width: 690px; height: 392px; border-radius: 18px; overflow: hidden; }
  .card-front { top: 89px; background: var(--card-white); }
  .card-back { top: 547px; background: var(--card-dark); }

  .brand-mark-faint {
    position: absolute; left: 350px; top: 0; width: 340px; height: 392px;
    background: radial-gradient(circle at 55% 48%, #e6e6e6 0%, #ececec 40%, rgba(244,244,244,0) 72%);
  }

  .wordmark {
    position: absolute; left: 32px; top: 36px;
    font-weight: 800; font-size: 44px; line-height: 48px; letter-spacing: -1px;
    color: var(--brand-blue); text-transform: uppercase;
  }

  .name-tab { position: absolute; left: 0; top: 186px; width: 18px; height: 43px; background: var(--brand-blue); border-radius: 0 5px 5px 0; }
  .person-name { position: absolute; left: 33px; top: 183px; font-weight: 700; font-size: 26px; letter-spacing: 0.5px; color: var(--brand-blue); text-transform: uppercase; }
  .person-title { position: absolute; left: 34px; top: 211px; font-weight: 500; font-size: 17px; color: var(--ink); letter-spacing: 0.3px; }

  .contact-list { position: absolute; left: 31px; top: 253px; list-style: none; }
  .contact-list li { display: flex; align-items: center; height: 28px; font-size: 17.5px; font-weight: 500; color: var(--ink); letter-spacing: 0.4px; }
  .contact-list svg { width: 13px; height: 13px; margin-right: 8px; fill: var(--brand-blue); flex: none; }

  .address { position: absolute; right: 33px; top: 314px; text-align: right; font-size: 17.5px; font-weight: 500; line-height: 22px; color: var(--ink); letter-spacing: 0.4px; }

  .back-pattern {
    position: absolute; inset: 0;
    background: linear-gradient(105deg, #262626 0%, #2e2e2e 35%, #4a4a4a 70%, var(--pattern-light) 100%);
  }
  .services { position: absolute; left: 0; width: 690px; padding-right: 30px; top: 297px; text-align: center; font-size: 17.5px; font-weight: 500; color: var(--back-text); letter-spacing: 0.5px; }
  .services .dot { color: var(--brand-blue); margin: 0 6px; }
  .tagline { position: absolute; left: 0; width: 690px; padding-right: 30px; top: 325px; text-align: center; font-size: 17.5px; font-weight: 500; color: var(--back-text); letter-spacing: 0.5px; }
  .back-logo { position: absolute; left: 548px; top: 304px; display: flex; align-items: center; gap: 4px; color: var(--brand-blue); font-weight: 700; font-size: 10px; line-height: 12px; width: 90px; }
  .back-logo .disc { width: 10px; height: 10px; border-radius: 50%; background: var(--brand-blue); flex: none; }
</style>
</head>
<body>
  <section class="card card-front">
    <div class="brand-mark-faint" role="img" aria-label="Faint oversized brand mark in light grey"></div>
    <div class="wordmark">Flood<br>Rescue 360</div>
    <div class="name-tab"></div>
    <div class="person-name">Marcus Pelley</div>
    <div class="person-title">General Manager</div>
    <ul class="contact-list">
      <li><svg viewBox="0 0 16 16" aria-hidden="true"><path d="M1 6c0-2 3-4 7-4s7 2 7 4v1h-4V5.5C10 5 6 5 5 5.5V7H1z"/><path d="M3 8h10l1 6H2z"/></svg>469-555-0148</li>
      <li><svg viewBox="0 0 16 16" aria-hidden="true"><path d="M4 0h8a1 1 0 0 1 1 1v14a1 1 0 0 1-1 1H4a1 1 0 0 1-1-1V1a1 1 0 0 1 1-1zm1 2v10h6V2zm3 11a1 1 0 1 0 0 2 1 1 0 0 0 0-2z"/></svg>214-555-0193</li>
      <li><svg viewBox="0 0 16 16" aria-hidden="true"><path d="M8 1l7 5v9H1V6zm0 2L3 6.5 8 10l5-3.5z"/></svg>Marcus@FloodRescue360.example</li>
      <li><svg viewBox="0 0 16 16" aria-hidden="true"><path d="M8 0a8 8 0 1 0 0 16A8 8 0 0 0 8 0zm-1 2l1 3-3 2 1 3-2 1-2-4c1-3 3-5 5-5zm4 1c2 1 3 3 3 5l-3 4-1-3 1-3z"/></svg>www.FloodRescue360.example</li>
    </ul>
    <div class="address">2650 Harbor Ridge Rd #310<br>Mesquite, TX 75150</div>
  </section>

  <section class="card card-back">
    <div class="back-pattern" role="img" aria-label="Repeating grid of brand marks fading from dark to light grey"></div>
    <div class="services">Water<span class="dot">•</span>Fire<span class="dot">•</span>Mold<span class="dot">•</span>Reconstruction</div>
    <div class="tagline">Urgency for Your Water Emergency!</div>
    <div class="back-logo"><span class="disc"></span><span>Flood Rescue 360</span></div>
  </section>
</body>
</html>
```